Redesign of Form/Document Navigation Page

I need a redesign of our document and navigation bar on the left. We want the same navigation bar layout/setup but want the buttons and typography to be simple and matching all over. The form needs to be aesthetically pleasing and fit within the page.

1st attachment is our Direct Deposit and the second is the form continued.

```html
<!DOCTYPE html>
<html lang="en">
<head>
<meta charset="utf-8">
<title>Direct Deposit – Northgate Patrol Services</title>
<link href="https://fonts.googleapis.com/css2?family=Open+Sans:wght@400;600;700&family=Raleway:wght@400;500&display=swap" rel="stylesheet">
<style>
  :root{
    --gold:#f0b323;
    --ink:#222;
    --muted:#777;
    --nav-bg:#ececec;
    --line:#d6d6d6;
    --white:#fff;
  }
  *{box-sizing:border-box;margin:0;padding:0}
  html,body{width:1200px;height:862px;overflow:hidden;background:var(--white);font-family:"Open Sans",sans-serif;color:var(--ink)}
  .page{position:relative;width:1200px;height:862px}
  .topbar{position:absolute;left:0;top:0;width:1200px;height:66px;border-bottom:1px solid #e2e2e2;background:var(--white)}
  .brand{position:absolute;left:40px;top:12px;display:flex;align-items:center;gap:8px}
  .brand-dot{width:34px;height:34px;border-radius:50%;background:var(--gold)}
  .brand-name{font-weight:700;font-size:15px;line-height:17px;color:var(--gold);text-transform:uppercase;width:170px}
  .btn-back{position:absolute;left:297px;top:18px;width:124px;height:31px;background:var(--gold);color:var(--white);font-size:11.5px;display:flex;align-items:center;justify-content:center;gap:6px;border-radius:2px}
  .toplink{position:absolute;top:22px;display:flex;align-items:center;gap:8px;font-size:12.5px;color:#444}
  .user{position:absolute;left:962px;top:14px;display:flex;align-items:center;gap:9px;font-size:12.5px;color:#444}
  .avatar{width:40px;height:40px;border-radius:50%;background:linear-gradient(135deg,#c9a27e,#7a5a45)}
  .power{position:absolute;left:1134px;top:18px}
  .sidenav{position:absolute;left:0;top:67px;width:289px;height:551px;background:var(--nav-bg);border-right:1px solid #ddd}
  .nav-item{height:79px;display:flex;align-items:center;padding-left:25px;gap:13px;border-bottom:1px solid #dadada;font-family:"Raleway",sans-serif;font-size:14.5px;color:#444}
  .nav-item.active{background:var(--gold);color:var(--white);border-bottom-color:var(--gold)}
  .nav-icon{width:50px;height:50px;border-radius:50%;background:var(--white);border:1px solid #d3d3d3;display:flex;align-items:center;justify-content:center;flex:none}
  .content{position:absolute;left:347px;top:0}
  .notice{position:absolute;top:104px;left:0;width:780px;font-size:13px}
  .legal{position:absolute;top:136px;left:1px;width:780px;font-size:11px;line-height:22px;color:var(--muted)}
  .legal p+p{margin-top:5px}
  .label{position:absolute;font-size:13px;white-space:nowrap}
  .field{position:absolute;border:1px solid #cfcfcf;border-radius:2px;background:var(--white);font-size:12.5px;color:#999;padding:10px 13px}
  .sign-line{position:absolute;height:1px;background:#cfcfcf}
  .btn{position:absolute;background:var(--gold);color:var(--white);font-size:16px;display:flex;align-items:center;justify-content:center;gap:10px;border-radius:2px}
  .manager{position:absolute;left:2px;top:487px;width:792px;height:274px;border:1px solid #cfcfcf}
  .manager h2{position:absolute;left:42px;top:28px;font-weight:400;font-size:27px;color:#333}
  .footer{position:absolute;left:0;top:823px;width:1200px;border-top:1px solid #e2e2e2;height:39px;font-size:11.5px;color:#555}
  .footer .copy{position:absolute;left:0;right:0;top:12px;text-align:center}
  .footer .code{position:absolute;right:15px;top:12px}
</style>
</head>
<body>
<div class="page">
  <header class="topbar">
    <div class="brand"><span class="brand-dot"></span><span class="brand-name">Northgate Patrol Services</span></div>
    <div class="btn-back">
      <svg width="15" height="12" viewBox="0 0 15 12" fill="none" stroke="#fff" stroke-width="1.4"><path d="M6 1L1 5.5 6 10M1 5.5h8a5 5 0 0 1 5 5"/></svg>Back to Profile
    </div>
    <div class="toplink" style="left:447px">
      <svg width="20" height="18" viewBox="0 0 20 18" fill="none" stroke="#f0b323" stroke-width="1.5"><path d="M1 9L10 1l9 8M4 7v10h4v-5h4v5h4V7"/></svg>Home
    </div>
    <div class="toplink" style="left:537px">
      <svg width="20" height="20" viewBox="0 0 20 20" fill="none" stroke="#f0b323" stroke-width="1.5"><circle cx="10" cy="10" r="9"/><path d="M10 8v6M10 5v1"/></svg>Help
    </div>
    <div class="user"><div class="avatar" role="img" aria-label="User profile photo"></div>Mara Ellison
      <svg width="10" height="6" viewBox="0 0 10 6" fill="none" stroke="#555" stroke-width="1.3"><path d="M1 1l4 4 4-4"/></svg>
    </div>
    <svg class="power" width="32" height="32" viewBox="0 0 32 32" fill="none" stroke="#f0b323" stroke-width="2.2" stroke-linecap="round"><path d="M9 8a12 12 0 1 0 14 0"/><path d="M16 2v12"/></svg>
  </header>

  <nav class="sidenav">
    <div class="nav-item active"><span class="nav-icon"><svg width="28" height="28" viewBox="0 0 28 28" fill="#f0b323"><path d="M13 2h2v7h3l-4 4-4-4h3z"/><ellipse cx="8" cy="16" rx="5" ry="2"/><ellipse cx="8" cy="20" rx="5" ry="2"/><ellipse cx="8" cy="24" rx="5" ry="2"/><ellipse cx="20" cy="19" rx="5" ry="2"/><ellipse cx="20" cy="23" rx="5" ry="2"/></svg></span>Direct Deposit</div>
    <div class="nav-item"><span class="nav-icon"><svg width="28" height="22" viewBox="0 0 28 22" fill="none" stroke="#555" stroke-width="2.2"><path d="M6 4a9 9 0 0 0 0 14M22 4a9 9 0 0 1 0 14"/><text x="14" y="16" text-anchor="middle" font-size="14" font-weight="700" fill="#555" stroke="none" font-family="Open Sans,sans-serif">$</text></svg></span>Change W-4</div>
    <div class="nav-item"><span class="nav-icon"><svg width="26" height="24" viewBox="0 0 26 24" fill="#555"><rect x="1" y="3" width="2" height="18"/><rect x="5" y="3" width="1.5" height="12"/><rect x="9" y="3" width="2.5" height="8"/><rect x="19" y="3" width="2" height="18"/><rect x="23" y="3" width="2" height="18"/><circle cx="13" cy="15" r="4" fill="none" stroke="#555" stroke-width="2"/><path d="M10 18l-4 4" stroke="#555" stroke-width="2"/></svg></span>Labour Code</div>
    <div class="nav-item"><span class="nav-icon"><svg width="28" height="22" viewBox="0 0 28 22" fill="#555"><circle cx="8" cy="6" r="4"/><path d="M1 20c0-6 3-8 7-8s7 2 7 8z"/><rect x="16" y="4" width="11" height="2.5"/><rect x="16" y="10" width="11" height="2.5"/><rect x="16" y="16" width="11" height="2.5"/></svg></span>Personal Information</div>
    <div class="nav-item"><span class="nav-icon"><svg width="28" height="28" viewBox="0 0 28 28" fill="#555"><circle cx="14" cy="4" r="3"/><path d="M9 12c0-3 2-4 5-4s5 1 5 4z"/><circle cx="5" cy="17" r="3"/><path d="M0 26c0-4 2-5 5-5s5 1 5 5z"/><circle cx="23" cy="17" r="3"/><path d="M18 26c0-4 2-5 5-5s5 1 5 5z"/><path d="M11 17h6" stroke="#555" stroke-width="2"/></svg></span>Appraisal and Review</div>
    <div class="nav-item"><span class="nav-icon"><svg width="30" height="26" viewBox="0 0 30 26" fill="none" stroke="#555" stroke-width="1.8"><rect x="2" y="12" width="22" height="12"/><path d="M6 17h7M6 20h5M14 14L26 2l2 2-12 12h-2z"/><text x="20" y="22" font-size="7" fill="#555" stroke="none" font-family="Open Sans,sans-serif">$</text></svg></span>Write Up-Slip</div>
    <div class="nav-item"><span class="nav-icon"><svg width="30" height="26" viewBox="0 0 30 26" fill="#555"><rect x="4" y="20" width="2" height="5"/><rect x="9" y="17" width="2" height="8"/><rect x="14" y="14" width="2" height="11"/><rect x="19" y="11" width="2" height="14"/><rect x="24" y="8" width="2" height="17"/><path d="M1 17L26 2M22 2h4v4" fill="none" stroke="#555" stroke-width="1.6"/></svg></span>Employee Performance</div>
  </nav>

  <main class="content">
    <p class="notice">IMPORTANT! Please read and sign before completing and submitting.</p>
    <div class="legal">
      <p>I hereby authorize NORTHGATE PATROL SERVICES to deposit any amounts owed me, as instructed by my employer, by initiating credit entries to my account at the financial institution (hereinafter "Bank") indicated on this form. Further, I authorize Bank to accept and to credit any credit entries indicated by NORTHGATE PATR</p>
      <p>indicated on this form. Further, I authorize Bank to accept and to credit any credit entries indicated by NORTHGATE PATR</p>
    </div>

    <span class="label" style="left:1px;top:276px">Employee name :</span>
    <div class="field" style="left:151px;top:267px;width:238px;height:35px"></div>

    <span class="label" style="left:2px;top:344px">Employee Signature :</span>
    <div class="sign-line" style="left:152px;top:359px;width:240px"></div>
    <span class="label" style="left:552px;top:344px">Sign Date :</span>
    <div class="sign-line" style="left:625px;top:359px;width:166px"></div>

    <div class="btn" style="left:2px;top:399px;width:194px;height:43px">
      <svg width="17" height="16" viewBox="0 0 17 16" fill="none" stroke="#fff" stroke-width="1.8"><path d="M13 9v5H1V2h9"/><path d="M4 7l3 3 9-9"/></svg>Accept Document
    </div>

    <section class="manager">
      <h2>Only payroll manager signs below</h2>
      <div class="field" style="left:46px;top:87px;width:319px;height:35px;padding-top:9px">Company Name</div>
      <div class="field" style="left:46px;top:139px;width:319px;height:35px;padding-top:9px">Employee file number</div>
      <div class="field" style="left:383px;top:87px;width:319px;height:87px;padding-top:10px">Comments</div>
      <div class="btn" style="left:46px;top:193px;width:125px;height:43px">
        <svg width="17" height="16" viewBox="0 0 17 16" fill="none" stroke="#fff" stroke-width="1.8"><path d="M13 9v5H1V2h9"/><path d="M4 7l3 3 9-9"/></svg>Submit
      </div>
    </section>
  </main>

  <footer class="footer">
    <div class="copy">Copyright © 2016. Northgate Patrol Services. All Rights Reserved</div>
    <div class="code">C8</div>
  </footer>
</div>
</body>
</html>
```